MRT Property - Business Cards

Looking for a business card & general letterhead, signage etc design for our new logo.

Colours:
000a20
0056a2
00b5ef
0088ce
68cef2

Fonts:
Poppins
Karla

Please keep look and feel of new brand - example in the zip package I sent.

```html
<!DOCTYPE html>
<html lang="en">
<head>
<meta charset="utf-8">
<title>MRT Property – Business Cards</title>
<link rel="stylesheet" href="https://fonts.googleapis.com/css2?family=Montserrat:wght@400;500;700&display=swap">
<style>
  :root{
    --ink:#000a20;
    --navy:#0056a2;
    --cyan:#00b5ef;
    --blue:#0088ce;
    --sky:#68cef2;
    --paper:#ffffff;
    --backdrop:#e9e6e1;
  }
  *{margin:0;padding:0;box-sizing:border-box}
  html,body{width:1200px;height:931px;overflow:hidden}
  body{background:var(--backdrop);font-family:"Montserrat",sans-serif;color:var(--ink);position:relative}
  .card{position:absolute;width:560px;height:320px;background:var(--paper);border-radius:18px;box-shadow:0 10px 28px rgba(0,10,32,.18)}
  .card-front{left:60px;top:60px;display:flex;align-items:center;justify-content:center}
  .card-back{left:580px;top:551px}
  .brand{display:flex;align-items:center;gap:14px}
  .brand-dot{width:34px;height:34px;border-radius:50%;background:var(--blue)}
  .brand-name{font-weight:700;color:var(--navy);font-size:44px;letter-spacing:.5px}
  .card-back .brand{position:absolute;right:36px;top:34px;gap:10px}
  .card-back .brand-dot{width:22px;height:22px}
  .card-back .brand-name{font-size:28px}
  .divider{position:absolute;left:34px;right:34px;top:186px;height:2px;background:var(--blue)}
  .person{position:absolute;left:34px;top:130px}
  .person-name{font-weight:700;color:var(--navy);font-size:22px;line-height:1.1}
  .person-role{font-size:13px;margin-top:4px}
  .contacts{position:absolute;left:34px;top:204px;list-style:none;font-size:13px}
  .contacts li{display:flex;align-items:center;gap:10px;height:26px}
  .contacts svg{width:14px;height:14px;fill:var(--navy)}
  .address{position:absolute;right:34px;top:204px;text-align:right;font-size:12.5px;line-height:1.5}
</style>
</head>
<body>
  <section class="card card-front">
    <div class="brand">
      <span class="brand-dot"></span>
      <span class="brand-name">MRT Property</span>
    </div>
  </section>

  <section class="card card-back">
    <div class="brand">
      <span class="brand-dot"></span>
      <span class="brand-name">MRT Property</span>
    </div>
    <div class="person">
      <div class="person-name">Daniel Hart</div>
      <div class="person-role">Mnaging Director</div>
    </div>
    <div class="divider"></div>
    <ul class="contacts">
      <li><svg viewBox="0 0 24 24"><path d="M6.6 10.8a15.1 15.1 0 0 0 6.6 6.6l2.2-2.2c.3-.3.7-.4 1-.2 1.1.4 2.3.6 3.6.6.6 0 1 .4 1 1V20c0 .6-.4 1-1 1A17 17 0 0 1 3 4c0-.6.4-1 1-1h3.5c.6 0 1 .4 1 1 0 1.3.2 2.5.6 3.6.1.3 0 .7-.2 1z"/></svg>1 (555) 014-2731</li>
      <li><svg viewBox="0 0 24 24"><path d="M2 5h20v14H2zm2 2v.5l8 5 8-5V7l-8 5z"/></svg>info@mrtproperty.com</li>
      <li><svg viewBox="0 0 24 24"><circle cx="12" cy="12" r="10"/></svg>www.mrtproperty.com</li>
    </ul>
    <div class="address">480 Maple Ridge Ave Suite<br>210 Dayton Ohio 45402</div>
  </section>
</body>
</html>
```